Whimsical business cards and stationary for accessories and gifts company
Please use your design expertise!
Whimsical business cards and stationary for accessories and gifts company - Children
Creative Brief
Bright & Fun-filled
Marisa J Tavelmor
Designer
Marlow Falls, Ohio
LulaandPipDesigns@brightpost.net
www.LulaAndPipDesigns.craftnook.net www.friendwall.net/LulaandPipDesigns @LulaAndPipDesigns
Hair Accessories Party Favors Unique Gifts
Concepts
Business Cards for kids golf
Xpert Xpert
Kindly upload the Ai file of your logo.

```html
<!DOCTYPE html>
<html lang="en">
<head>
<meta charset="utf-8">
<title>Lula &amp; Pip Business Cards</title>
<link href="https://fonts.googleapis.com/css2?family=Raleway:wght@300;400;500&display=swap" rel="stylesheet">
<style>
  :root {
    --plum: #8d2a8c;
    --plum-soft: #a44aa3;
    --ink: #4a4a4a;
    --muted: #7a7a7a;
    --rule: #cfcfcf;
    --card: #ffffff;
    --backdrop: #e9e6e2;
  }
  * { margin: 0; padding: 0; box-sizing: border-box; }
  html, body {
    width: 1200px; height: 904px; overflow: hidden;
    background: var(--backdrop);
    font-family: "Raleway", sans-serif;
  }
  .card {
    position: absolute;
    width: 630px; height: 360px;
    background: var(--card);
    box-shadow: 0 10px 28px rgba(0,0,0,.18);
    overflow: hidden;
  }
  .card--front { left: 70px; top: 60px; }
  .card--back { left: 500px; top: 484px; }

  .brand {
    display: flex; align-items: center; gap: 12px;
    color: var(--plum); font-weight: 500; white-space: nowrap;
  }
  .brand__dot { border-radius: 50%; background: var(--plum); flex: none; }
  .card--front .brand {
    position: absolute; left: 0; right: 0; top: 110px;
    justify-content: center; font-size: 44px;
  }
  .card--front .brand__dot { width: 34px; height: 34px; }
  .services {
    position: absolute; left: 0; right: 0; bottom: 58px;
    text-align: center; color: var(--plum);
    font-size: 15px; letter-spacing: .3px;
  }
  .services .sep { margin: 0 12px; color: var(--plum-soft); }

  .identity { position: absolute; left: 30px; top: 130px; width: 290px; }
  .card--back .brand { font-size: 38px; }
  .card--back .brand__dot { width: 26px; height: 26px; }
  .identity__tag {
    margin-top: 6px; padding-left: 40px;
    font-size: 11px; color: var(--plum-soft); letter-spacing: 1px;
  }
  .divider {
    position: absolute; left: 338px; top: 50px; width: 1px; height: 260px;
    background: var(--rule);
  }
  .details {
    position: absolute; left: 356px; top: 52px; width: 266px;
    color: var(--ink);
  }
  .details__name { color: var(--plum); font-size: 20px; font-weight: 500; }
  .details__role { font-size: 13px; color: var(--muted); margin-top: 2px; }
  .details__place { font-size: 12.5px; margin-top: 14px; padding-left: 20px; }
  .contact { list-style: none; margin-top: 4px; }
  .contact li {
    display: flex; align-items: center; gap: 8px;
    font-size: 12px; line-height: 21px; white-space: nowrap;
  }
  .contact__icon {
    width: 12px; height: 12px; flex: none; background: var(--plum); border-radius: 2px;
  }
  .contact svg { width: 12px; height: 12px; flex: none; }
  .band {
    position: absolute; left: 0; right: 0; bottom: 0; height: 10px;
    background: var(--plum);
  }
</style>
</head>
<body>
  <section class="card card--front" aria-label="Card front">
    <div class="brand"><span class="brand__dot"></span>Lula &amp; Pip</div>
    <p class="services">Hair Accessories<span class="sep">|</span>Party Favors<span class="sep">|</span>Unique Gifts</p>
  </section>

  <section class="card card--back" aria-label="Card back">
    <div class="identity">
      <div class="brand"><span class="brand__dot"></span>Lula &amp; Pip</div>
      <p class="identity__tag">little gift boutique</p>
    </div>
    <div class="divider"></div>
    <div class="details">
      <p class="details__name">Marisa J Tavelmor</p>
      <p class="details__role">Designer</p>
      <p class="details__place">Marlow Falls, Ohio</p>
      <ul class="contact">
        <li>
          <svg viewBox="0 0 12 12"><rect width="12" height="12" rx="2" fill="var(--plum)"/><path d="M3 3.2l1.6-.4.8 1.8-1 .7a5 5 0 0 0 2.3 2.3l.7-1 1.8.8-.4 1.6C5.8 9 3 6.2 3 3.2z" fill="#fff"/></svg>
          (555) 014-2738
        </li>
        <li>
          <svg viewBox="0 0 12 12"><rect width="12" height="12" rx="2" fill="var(--plum)"/><rect x="2.5" y="3.5" width="7" height="5" fill="none" stroke="#fff" stroke-width=".9"/><path d="M2.5 3.5L6 6.5l3.5-3" fill="none" stroke="#fff" stroke-width=".9"/></svg>
          LulaandPipDesigns@brightpost.net
        </li>
        <li><span class="contact__icon"></span>www.LulaAndPipDesigns.craftnook.net</li>
        <li><span class="contact__icon"></span>www.friendwall.net/LulaandPipDesigns</li>
        <li><span class="contact__icon"></span>@LulaAndPipDesigns</li>
      </ul>
    </div>
    <div class="band"></div>
  </section>
</body>
</html>
```